Business Card Design

We are a commercial real estate brokerage in San Francisco, leasing office buildings downtown.
I would like a clean, elegant look. Simple but powerful .

Industry/Entity Type

Business

Contact Information for Business Card

Derek Holloway
lic# 07258143
415.555.0172
derek@velt-commercial.example
velt-commercial.example

```html
<!DOCTYPE html>
<html lang="en">
<head>
<meta charset="utf-8">
<title>Velt Commercial – Business Card</title>
<link href="https://fonts.googleapis.com/css2?family=Open+Sans:wght@300;600;700&display=swap" rel="stylesheet">
<style>
  :root {
    --page-bg: #e9e6e1;
    --card-white: #ffffff;
    --slate-blue: #7486a3;
    --swoosh-grey: #5f5f61;
    --ink-dark: #4a4a4c;
    --text-light: #ffffff;
  }
  html, body {
    margin: 0;
    padding: 0;
    width: 1200px;
    height: 806px;
    overflow: hidden;
    background: var(--page-bg);
    font-family: "Open Sans", Arial, sans-serif;
  }
  .business-card {
    position: absolute;
    left: 80px;
    top: 103px;
    width: 1040px;
    height: 599px;
    border-radius: 32px;
    overflow: hidden;
    background: var(--card-white);
    box-shadow: 0 2px 6px rgba(0,0,0,0.12);
  }
  .card-backdrop {
    position: absolute;
    inset: 0;
  }
  .brand {
    position: absolute;
    left: 0;
    right: 0;
    top: 70px;
    display: flex;
    justify-content: center;
    align-items: center;
    gap: 34px;
  }
  .brand-square {
    width: 120px;
    height: 120px;
    background: var(--slate-blue);
  }
  .brand-name {
    color: var(--ink-dark);
    font-weight: 600;
    line-height: 1;
    letter-spacing: 1px;
  }
  .brand-name .line-main {
    display: block;
    font-size: 112px;
  }
  .brand-name .line-sub {
    display: block;
    font-size: 48px;
    margin-top: 6px;
    letter-spacing: 2px;
  }
  .website {
    position: absolute;
    left: 0;
    right: 0;
    top: 262px;
    text-align: center;
    font-size: 30px;
    font-weight: 600;
    color: var(--ink-dark);
    display: flex;
    justify-content: center;
    align-items: center;
    gap: 8px;
  }
  .agent {
    position: absolute;
    right: 614px;
    top: 422px;
    text-align: right;
    color: var(--text-light);
  }
  .agent-name {
    font-size: 32px;
    font-weight: 700;
    line-height: 1.2;
  }
  .agent-licence {
    font-size: 30px;
    font-weight: 300;
    line-height: 1.3;
  }
  .divider {
    position: absolute;
    left: 450px;
    top: 414px;
    width: 3px;
    height: 123px;
    background: var(--ink-dark);
  }
  .contact {
    position: absolute;
    left: 472px;
    top: 424px;
    color: var(--text-light);
    font-weight: 700;
    font-size: 28px;
  }
  .contact-row {
    display: flex;
    align-items: center;
    gap: 10px;
    height: 42px;
  }
</style>
</head>
<body>
  <div class="business-card">
    <svg class="card-backdrop" width="1040" height="599" viewBox="0 0 1040 599">
      <path d="M0 258 Q500 470 1040 214 L1040 599 L0 599 Z" fill="var(--slate-blue)"/>
      <path d="M0 222 Q500 470 1040 178 L1040 196 Q500 480 0 238 Z" fill="var(--swoosh-grey)"/>
    </svg>

    <div class="brand">
      <div class="brand-square"></div>
      <div class="brand-name">
        <span class="line-main">VELT</span>
        <span class="line-sub">COMMERCIAL</span>
      </div>
    </div>

    <div class="website">
      <svg width="28" height="28" viewBox="0 0 28 28" aria-hidden="true">
        <g fill="none" stroke="var(--slate-blue)" stroke-width="2">
          <circle cx="14" cy="14" r="12"/>
          <ellipse cx="14" cy="14" rx="5" ry="12"/>
          <line x1="2" y1="14" x2="26" y2="14"/>
        </g>
      </svg>
      <span>velt-commercial.example</span>
    </div>

    <div class="agent">
      <div class="agent-name">Derek Holloway</div>
      <div class="agent-licence">Lic Nr. 07258143</div>
    </div>

    <div class="divider"></div>

    <div class="contact">
      <div class="contact-row">
        <svg width="22" height="30" viewBox="0 0 22 30" aria-hidden="true">
          <rect x="2" y="2" width="18" height="26" rx="3" fill="none" stroke="var(--text-light)" stroke-width="2.5"/>
          <line x1="8" y1="23" x2="14" y2="23" stroke="var(--text-light)" stroke-width="2"/>
        </svg>
        <span>415.555.0172</span>
      </div>
      <div class="contact-row">
        <svg width="30" height="22" viewBox="0 0 30 22" aria-hidden="true">
          <rect x="2" y="2" width="26" height="18" fill="none" stroke="var(--text-light)" stroke-width="2.5"/>
          <polyline points="2,2 15,13 28,2" fill="none" stroke="var(--text-light)" stroke-width="2.5"/>
        </svg>
        <span>derek@velt-commercial.example</span>
      </div>
    </div>
  </div>
</body>
</html>
```